Defense Attorney Business Card Design Project/ Stationary

I am looking for a distinctive business card design for my solo law practice.
I practice criminal defense, both juvenile and adult, including DUI. I am a very experienced attorney with prior military experience. The design should convey a traditional, old school flair, but not be too stodgy or uptight. Some color. My logo should appear.
Updates

Project Deadline Extended Reason: I misunderstood how this project works and I was not prepared with my logo when this project ran the first time. Added Thursday, November 13, 2014

Project Deadline Extended
Reason: I was sent overseas on military duty last year, which interrupted this project. Thank you for your participation... I hope we can get this done this week! Thank you, Neil

Target Market(s)

Regular everyday people looking for strong, knowledgeable, authoritative representation while they are faced with criminal charges. Many have never been charged with a crime before. A reassuring air is therefore desired.

Industry/Entity Type

Business

Contact Information for Business Card

My information is:
Theodore M. Quill, Attorney at Law
785 Birch Avenue Suite 300
Oakland, California 94719
Tel: (510) 384-6125
Fax: (510) 391-7802
email: neilquilllaw@mailvine.example
web: www.neilquilllaw.example

Font styles to use
Serif
Sans Serif
Decorative

Colors
0255a3
ffffff

Requirements
Must have
• Sharp lines, bold elements. Conservative use of colors, such as deep blues, burgundy, grays for example.
• While my logo says "Theodore M. Quill", it should be modified to show "Theodore M. Quill".
Should not have
• Cliche imagery such as scales of justice, gavels, Statue of Liberty, etc.

```html
<!DOCTYPE html>
<html lang="en">
<head>
<meta charset="utf-8">
<title>Theodore M. Quill – Business Card</title>
<link href="https://fonts.googleapis.com/css2?family=Exo+2:wght@400;500&display=swap" rel="stylesheet">
<style>
  :root{
    --page:#e9e8e5;
    --card-top:#f4f3f0;
    --card-bottom:#e6e4df;
    --ink:#2f2f31;
    --navy:#0d4464;
    --band-dark:#2b2b2d;
    --band-light:#4a4a4c;
    --rule:#9a9a9a;
    --white:#ffffff;
  }
  *{margin:0;padding:0;box-sizing:border-box}
  html,body{width:1200px;height:768px;overflow:hidden;background:var(--page)}
  body{position:relative;font-family:"Exo 2",sans-serif;color:var(--ink)}
  .card{
    position:absolute;left:100px;top:93px;width:1000px;height:582px;
    border-radius:22px;overflow:hidden;
    background:linear-gradient(160deg,var(--card-top),var(--card-bottom));
    box-shadow:0 10px 30px rgba(0,0,0,.15);
  }
  .holder-name{position:absolute;left:43px;top:196px;font-size:27px;font-weight:500;letter-spacing:1.5px;text-transform:uppercase}
  .holder-title{position:absolute;left:43px;top:240px;font-size:22px;font-weight:500;color:var(--navy);letter-spacing:.4px}
  .divider{position:absolute;left:61px;top:287px;width:870px;height:2px;
    background:linear-gradient(90deg,rgba(154,154,154,0),var(--rule) 15%,var(--rule) 85%,rgba(154,154,154,0))}
  .brand-name{position:absolute;left:550px;top:200px;width:380px;text-align:center;
    font-size:38px;font-weight:500;color:var(--navy);letter-spacing:1px;white-space:nowrap}
  .address{position:absolute;left:43px;top:374px;font-size:21px;line-height:32px;letter-spacing:.6px;font-weight:500}
  .contacts{position:absolute;right:36px;top:306px;list-style:none;text-align:right}
  .contacts li{display:flex;justify-content:flex-end;align-items:center;gap:12px;font-weight:500;letter-spacing:.8px}
  .contacts .tel{font-size:21px;height:48px}
  .contacts .mail,.contacts .web{font-size:18px;height:34px}
  .contacts svg{width:22px;height:22px;fill:var(--navy);flex:none}
  .band{position:absolute;left:0;bottom:0;width:1000px;height:46px}
  .band-url{position:absolute;left:40px;bottom:12px;font-size:19px;color:var(--white);letter-spacing:.8px;font-weight:500}
</style>
</head>
<body>
  <div class="card">
    <p class="brand-name">Theodore M. Quill</p>

    <h1 class="holder-name">Theodore M. Quill</h1>
    <p class="holder-title">Attorney at Law</p>
    <div class="divider"></div>

    <p class="address">785 Birch Avenue Suite 300<br>Oakland, California 94719</p>

    <ul class="contacts">
      <li class="tel">(510) 384-6125
        <svg viewBox="0 0 24 24" aria-hidden="true"><path d="M6.6 10.8a15 15 0 0 0 6.6 6.6l2.2-2.2a1 1 0 0 1 1-.25 11.4 11.4 0 0 0 3.6.6 1 1 0 0 1 1 1V20a1 1 0 0 1-1 1A17 17 0 0 1 3 4a1 1 0 0 1 1-1h3.5a1 1 0 0 1 1 1c0 1.25.2 2.45.6 3.6a1 1 0 0 1-.25 1z"/></svg>
      </li>
      <li class="tel">(510) 384-6125
        <svg viewBox="0 0 24 24" aria-hidden="true"><path d="M7 1h10a2 2 0 0 1 2 2v18a2 2 0 0 1-2 2H7a2 2 0 0 1-2-2V3a2 2 0 0 1 2-2zm0 3v14h10V4zm5 15.5a1.2 1.2 0 1 0 0 2.4 1.2 1.2 0 0 0 0-2.4z"/></svg>
      </li>
      <li class="tel">(510) 391-7802
        <svg viewBox="0 0 24 24" aria-hidden="true"><path d="M8 2h8v5H8zM3 8h18a1 1 0 0 1 1 1v12a1 1 0 0 1-1 1H3a1 1 0 0 1-1-1V9a1 1 0 0 1 1-1zm2 3v3h3v-3zm5 0v2h9v-2zm0 4v2h2v-2zm4 0v2h2v-2zm4 0v2h2v-2z"/></svg>
      </li>
      <li class="mail">neilquilllaw@mailvine.example
        <svg viewBox="0 0 24 24" aria-hidden="true"><path d="M2 5h20v14H2zm2 2v.4l8 5.1 8-5.1V7zm0 2.8V17h16V9.8l-8 5.1z"/></svg>
      </li>
      <li class="web">www.neilquilllaw.example
        <svg viewBox="0 0 24 24" aria-hidden="true"><path d="M12 2a10 10 0 1 0 0 20 10 10 0 0 0 0-20zm6.9 6h-3a15 15 0 0 0-1.3-3.8A8 8 0 0 1 18.9 8zM12 4c.9 1.2 1.6 2.5 2 4h-4c.4-1.5 1.1-2.8 2-4zM4.3 14a8 8 0 0 1 0-4h3.4a16 16 0 0 0 0 4zm.8 2h3a15 15 0 0 0 1.3 3.8A8 8 0 0 1 5.1 16zm3-8h-3a8 8 0 0 1 4.3-3.8A15 15 0 0 0 8.1 8zM12 20c-.9-1.2-1.6-2.5-2-4h4c-.4 1.5-1.1 2.8-2 4zm2.3-6H9.7a14 14 0 0 1 0-4h4.6a14 14 0 0 1 0 4zm.3 5.8a15 15 0 0 0 1.3-3.8h3a8 8 0 0 1-4.3 3.8zm1.7-5.8a16 16 0 0 0 0-4h3.4a8 8 0 0 1 0 4z"/></svg>
      </li>
    </ul>

    <svg class="band" viewBox="0 0 1000 46" preserveAspectRatio="none" aria-hidden="true">
      <defs>
        <linearGradient id="darkBand" x1="0" y1="0" x2="1" y2="0">
          <stop offset="0" stop-color="#2b2b2d"/>
          <stop offset=".7" stop-color="#4a4a4c"/>
          <stop offset="1" stop-color="#2b2b2d"/>
        </linearGradient>
      </defs>
      <path d="M400 0 H1000 V46 H420 Q412 6 400 0 Z" fill="#0d4464"/>
      <path d="M0 0 H392 Q414 2 418 46 H0 Z" fill="url(#darkBand)"/>
    </svg>
    <p class="band-url">www.neilquilllaw.example</p>
  </div>
</body>
</html>
```